New Bicycle shop business card

Hi!
I'm looking for a business card for my new proffesional bike mechanics shop. This shop is only for fixing broken bikes and not selling bikes.
Peferbly a modern and sleek and modern design.
Colors: black, grey, red, white
Information:
Name: Rijwielwerkplaats Vanhoutte
Shop owner: Bart Vanhoutte & Marieke Segers
Website: www.rijwielwerkplaats-vanhoutte.be
Email: info@rijwielwerkplaats-vanhoutte.be
Phone number: +32471902368
Street adres: Kerkweg 46
9940 Bellebeke
Slogan/shop information: Herstellingen van alle merken.
Logo: see files.
Target Market(s)
People who seek a mechanic to fix or upgrade their bikes.
Contact Information for Business Card
Information:
Website: info@rijwielwerkplaats-vanhoutte.be
9940 Bellebeke
Logo: see files.

```html
<!DOCTYPE html>
<html lang="nl">
<head>
<meta charset="utf-8">
<title>Rijwielwerkplaats Vanhoutte – Visitekaartje</title>
<link href="https://fonts.googleapis.com/css2?family=Open+Sans:ital,wght@0,400;0,600;0,700;1,600&display=swap" rel="stylesheet">
<style>
  :root{
    --bg:#2a2d31;
    --card-black:#0b0b0c;
    --white:#ffffff;
    --red:#e4202f;
    --grey:#9a9a9a;
    --pattern:#141416;
  }
  *{box-sizing:border-box;margin:0;padding:0}
  html,body{width:1200px;height:900px;overflow:hidden}
  body{
    background:var(--bg);
    font-family:"Open Sans",Arial,sans-serif;
    position:relative;
  }
  .card{
    position:absolute;
    width:600px;height:343px;
    border-radius:28px;
    overflow:hidden;
    background:var(--card-black);
    box-shadow:0 18px 40px rgba(0,0,0,.45);
  }
  .card--front{left:300px;top:70px}
  .card--back{left:300px;top:487px}

  .front-shape{position:absolute;inset:0}

  .contact{
    position:absolute;left:36px;top:34px;
    color:var(--white);
  }
  .contact__label{color:var(--red);font-style:italic;font-weight:600;font-size:14px}
  .contact__owners{font-weight:700;font-size:17px;margin-top:2px}
  .contact__dash{width:10px;height:3px;background:var(--red);margin:12px 0}
  .contact__company{color:var(--red);font-weight:700;font-size:16px}
  .contact__role{font-size:12.5px;margin:2px 0 10px}
  .contact__line{display:flex;align-items:center;gap:8px;font-size:12.5px;line-height:20px}
  .contact__line svg{width:11px;height:11px;flex:none}
  .contact__address{font-size:12.5px}

  .brand{
    position:absolute;left:385px;top:128px;width:200px;
    display:flex;flex-direction:column;align-items:center;gap:12px;
  }
  .brand__dot{width:38px;height:38px;border-radius:50%;background:var(--red)}
  .brand__name{
    text-align:center;
    color:var(--card-black);
    font-weight:700;font-size:17px;line-height:1.25;letter-spacing:1px;
    text-transform:uppercase;
  }

  .back-pattern{
    position:absolute;inset:0;
    background:linear-gradient(135deg,var(--pattern),var(--card-black) 70%);
  }
  .back-brand{
    position:absolute;left:0;right:0;top:130px;
    display:flex;align-items:center;justify-content:center;gap:12px;
  }
  .back-brand__square{width:28px;height:28px;background:var(--red)}
  .back-brand__name{color:var(--white);font-weight:700;font-size:18px;letter-spacing:1px;text-transform:uppercase}
  .slogan{
    position:absolute;left:0;right:0;top:200px;text-align:center;
    color:var(--white);font-size:15px;font-weight:600;
  }
</style>
</head>
<body>

<section class="card card--front" aria-label="Voorzijde visitekaartje">
  <svg class="front-shape" viewBox="0 0 600 343" preserveAspectRatio="none" aria-hidden="true">
    <path d="M408 0 C350 80 332 200 345 343 L600 343 L600 0 Z" fill="#ffffff"/>
    <path d="M400 0 C342 80 324 200 337 343" fill="none" stroke="#e4202f" stroke-width="4"/>
  </svg>

  <div class="contact">
    <p class="contact__label">Shop owner:</p>
    <p class="contact__owners">Bart Vanhoutte &amp; Marieke Segers</p>
    <div class="contact__dash"></div>
    <p class="contact__company">Rijwielwerkplaats Vanhoutte</p>
    <p class="contact__role">General Manager</p>
    <p class="contact__line">
      <svg viewBox="0 0 12 12" aria-hidden="true"><path d="M2.5 1 4.5 1 5.3 3.6 4 4.6C4.7 6.1 5.9 7.3 7.4 8L8.4 6.7 11 7.5 11 9.5C11 10.3 10.3 11 9.5 11 5 11 1 7 1 2.5 1 1.7 1.7 1 2.5 1Z" fill="#e4202f"/></svg>
      +32471902368
    </p>
    <p class="contact__line">
      <svg viewBox="0 0 12 12" aria-hidden="true"><rect x="1" y="2.5" width="10" height="7" rx="1" fill="#e4202f"/><path d="M1.5 3 6 6.5 10.5 3" fill="none" stroke="#0b0b0c" stroke-width="1"/></svg>
      info@rijwielwerkplaats-vanhoutte.be
    </p>
    <p class="contact__line">
      <svg viewBox="0 0 12 12" aria-hidden="true"><circle cx="6" cy="6" r="5" fill="#e4202f"/><path d="M1 6H11M6 1C3.5 4 3.5 8 6 11M6 1C8.5 4 8.5 8 6 11" fill="none" stroke="#0b0b0c" stroke-width=".8"/></svg>
      www.rijwielwerkplaats-vanhoutte.be
    </p>
    <div class="contact__dash"></div>
    <p class="contact__address">Kerkweg 46 9940 Bellebeke</p>
  </div>

  <div class="brand">
    <div class="brand__dot"></div>
    <p class="brand__name">Rijwielwerkplaats<br>Vanhoutte</p>
  </div>
</section>

<section class="card card--back" aria-label="Achterzijde visitekaartje">
  <div class="back-pattern" role="img" aria-label="Faint repeating decorative pattern across the card background"></div>
  <div class="back-brand">
    <div class="back-brand__square"></div>
    <p class="back-brand__name">Rijwielwerkplaats Vanhoutte</p>
  </div>
  <p class="slogan">Herstellingen van alle merken.</p>
</section>

</body>
</html>
```